New letter head for Air Conditioning business

We need a new professional letter head design to suit our new re-branded air conditioning business. Our new logo is attached

```html
<!DOCTYPE html>
<html lang="en">
<head>
<meta charset="utf-8">
<title>Nordale Letterhead</title>
<link href="https://fonts.googleapis.com/css2?family=Arimo:wght@400;700&family=Open+Sans:wght@400;600&family=Homemade+Apple&display=swap" rel="stylesheet">
<style>
:root{
  --bg:#e9e9e9;
  --paper:#ffffff;
  --ink:#4a4a4a;
  --ink-dark:#2b2b2b;
  --coral:#ef6b5d;
  --green:#4cae6e;
  --line:#2f2f2f;
}
*{margin:0;padding:0;box-sizing:border-box}
html,body{width:1200px;height:795px;overflow:hidden;background:var(--bg)}
.letterhead{
  position:absolute;left:338px;top:28px;width:524px;height:740px;
  background:var(--paper);box-shadow:0 4px 18px rgba(0,0,0,.12);
  font-family:"Arimo",Arial,sans-serif;color:var(--ink);overflow:hidden;
}
.brand-header{position:absolute;right:44px;top:38px;text-align:right}
.brand-name{font-family:"Arimo",Arial,sans-serif;font-size:26px;font-weight:400;letter-spacing:5px;color:var(--ink-dark);line-height:1}
.brand-tagline{font-size:6px;letter-spacing:1.5px;color:var(--green);text-transform:uppercase;margin-top:3px}
.side-mark{position:absolute;left:48px;top:186px;display:flex;align-items:center;gap:6px}
.mark-dot{width:12px;height:12px;border-radius:50%;background:var(--coral)}
.mark-name{font-size:11px;letter-spacing:2px;color:var(--ink-dark)}
.corner-band{position:absolute;right:0;top:0;width:524px;height:740px}
.corner-mark{position:absolute;left:455px;top:300px;display:flex;flex-direction:column;align-items:center;gap:4px}
.corner-dot{width:26px;height:26px;border-radius:50%;background:var(--paper)}
.corner-name{font-size:9px;letter-spacing:1.5px;color:var(--paper)}
.letter{position:absolute;left:56px;top:236px;width:370px;font-size:8.6px;line-height:1.32}
.recipient p{margin:0}
.salutation{font-weight:700;margin:12px 0 12px}
.body-copy p{margin-bottom:12px}
.signoff{position:absolute;left:360px;top:236px;font-size:8.6px;line-height:1.35;width:110px}
.signature{font-family:"Homemade Apple",cursive;font-size:15px;color:#666;margin:10px 0 2px}
.contact-list{position:absolute;left:210px;top:610px;list-style:none;font-family:"Open Sans",Arial,sans-serif;font-size:8.4px;color:var(--ink-dark);line-height:1.55}
.contact-list li{display:flex;align-items:center;gap:6px}
.contact-icon{width:9px;height:9px;flex:none}
</style>
</head>
<body>
<article class="letterhead">
  <svg class="corner-band" viewBox="0 0 524 740" aria-hidden="true">
    <path d="M524 232 C470 236 428 286 438 332 C450 400 498 520 524 620 Z" fill="var(--coral)"/>
    <path d="M524 232 C470 236 428 286 438 332 C450 400 498 520 524 620" fill="none" stroke="var(--line)" stroke-width="3"/>
  </svg>

  <header class="brand-header">
    <div class="brand-name">NORDALE</div>
    <div class="brand-tagline">Air Conditioning Services</div>
  </header>

  <div class="side-mark"><span class="mark-dot"></span><span class="mark-name">NORDALE</span></div>

  <div class="corner-mark"><span class="corner-dot"></span><span class="corner-name">NORDALE</span></div>

  <section class="letter">
    <div class="recipient">
      <p>January 12, 2021</p>
      <p>Mr. John Doe</p>
      <p>President</p>
      <p>AA Corporation</p>
      <p>111 Street Name, Suite#</p>
      <p>City, State, 12345</p>
    </div>
    <p class="salutation">Dear Mr. John,</p>
    <div class="body-copy">
      <p>Lorem Ipsum is simply dummy text of the printing and typesetting industry. Lorem Ipsum has been the industry's standard dummy text ever since the 1500s, when an unknown printer took a galley of type and scrambled it to make a type specimen book. It has survived not only five centuries, but also the leap into electronic typesetting, remaining essentially unchanged.</p>
      <p>The standard chunk of Lorem Ipsum used since the 1500s is reproduced below for those interested. Sections 1.10.32 and 1.10.33 from "de Finibus Bonorum et Malorum" by Cicero are also reproduced in their exact original form, accompanied by English versions from the 1914 translation by H. Rackham.</p>
      <p>Lorem Ipsum is simply dummy text of the printing and typesetting industry. Lorem Ipsum has been the industry's standard dummy text ever since the 1500s, when an unknown printer took a galley of type and scrambled it to make a type specimen book. It has survived not only five centuries, but also the leap into electronic typesetting, remaining essentially unchanged. It was popularised in the</p>
    </div>
  </section>

  <div class="signoff">
    <p>Sincerely Your,</p>
    <p class="signature">your name</p>
    <p>Name Last Name</p>
    <p>Company Name</p>
  </div>

  <ul class="contact-list">
    <li><svg class="contact-icon" viewBox="0 0 10 10"><circle cx="5" cy="5" r="5" fill="var(--green)"/><path d="M3.2 2.6l1 1-.5.7c.4.8 1 1.4 1.8 1.8l.7-.5 1 1-.7.8C4.8 7.2 2.8 5.2 2.6 3.3z" fill="#fff"/></svg>(00) 05550 123 460</li>
    <li><svg class="contact-icon" viewBox="0 0 10 10"><circle cx="5" cy="5" r="5" fill="var(--green)"/><rect x="3" y="3" width="4" height="4" rx=".6" fill="#fff"/></svg>(00) 05550 123 461</li>
    <li><svg class="contact-icon" viewBox="0 0 10 10"><circle cx="5" cy="5" r="5" fill="var(--green)"/><rect x="2.6" y="3.2" width="4.8" height="3.6" fill="#fff"/><path d="M2.6 3.2L5 5.2 7.4 3.2" stroke="var(--green)" stroke-width=".6" fill="none"/></svg>hello@nordaleair.com</li>
    <li><svg class="contact-icon" viewBox="0 0 10 10"><circle cx="5" cy="5" r="5" fill="var(--green)"/><circle cx="5" cy="5" r="2.4" fill="none" stroke="#fff" stroke-width=".7"/><path d="M2.6 5h4.8" stroke="#fff" stroke-width=".6"/></svg>www.nordaleair.com</li>
    <li><svg class="contact-icon" viewBox="0 0 10 10"><circle cx="5" cy="5" r="5" fill="var(--green)"/><path d="M5 2.3a1.8 1.8 0 0 1 1.8 1.8C6.8 5.5 5 7.8 5 7.8S3.2 5.5 3.2 4.1A1.8 1.8 0 0 1 5 2.3z" fill="#fff"/></svg>Suite 102 Street name, State, Zip 2034, Country</li>
  </ul>
</article>
</body>
</html>
```